Custom PowerPoint Template for Training & Workshop Presentations

I am looking for a professional designer to create a custom PowerPoint template (PPTX) for my training and workshop materials. My trainings are designed for: HR professionals and Learning & Development specialists;
Executives and team leaders; Organizations investing in employee development and workplace learning; Participants in professional development workshops, seminars, and didactics trainings
The template should therefore appear trustworthy, calm, friendly, structured, and competence‑oriented. The design should be visually appealing, easy to read, and fully editable.

All branding files are attached to this project.
Please use them as the main reference for your design:
Logo (included as attachment)
Brand color specifications (included as attachment)
Font specifications related to the logo and brand (included as attachment)

What I need:
--> Title Slide: Title, subtitle, name, logo
(1–2 variations)
--> Agenda / Overview Slide
--> Content Slides
--> Text only
--> Text + image
-->Two-column
--> Section header
--> Quote / key message
--> Graphic / Model Slides: (1–2 layouts for frameworks, processes, models)
--> Tables & Charts: (Table styles in brand colors; Chart design aligned with typography and color palette)
--> Closing Slide: (Contact or call-to-action; Optional second variation)

All layouts must be built properly inside the PowerPoint Slide Master

```html
<!DOCTYPE html>
<html lang="en">
<head>
<meta charset="utf-8">
<title>Training Template Slides</title>
<link rel="stylesheet" href="https://fonts.googleapis.com/css2?family=Inter:wght@400;500;600&display=swap">
<style>
:root{
  --canvas:#e2e3e6;
  --navy:#123f7a;
  --blue:#1f4f8c;
  --sky:#2f8ac6;
  --steel:#7b9bb8;
  --ink:#1b1f27;
  --muted:#4a4f57;
  --card:#e3ebf2;
  --white:#ffffff;
  --grid:#e4e6ea;
}
*{box-sizing:border-box;margin:0;padding:0}
html,body{width:1013px;height:1200px;overflow:hidden;background:var(--canvas);font-family:'Inter',sans-serif;color:var(--ink)}
.slide{position:absolute;width:440px;height:248px;background:var(--white);overflow:hidden}
.abs{position:absolute}
.brand{position:absolute;display:flex;align-items:center;gap:6px;height:22px}
.brand-mark{width:12px;height:12px;border:1.3px solid var(--blue);border-radius:2px}
.brand-name{font-weight:600;font-size:10px;color:var(--blue);line-height:1.1;white-space:nowrap}
.brand.light .brand-mark{border-color:var(--white)}
.brand.light .brand-name{color:var(--white)}
.head-rule{position:absolute;width:1px;height:22px;background:var(--blue)}
.slide-title{position:absolute;font-size:11.5px;font-weight:500;color:var(--blue)}
.hline{position:absolute;height:1px;background:var(--blue)}
.photo{position:absolute}
.agenda-item{position:absolute;display:flex;gap:8px;width:160px}
.agenda-num{flex:none;width:19px;height:19px;border-radius:50%;background:var(--navy);color:var(--white);font-size:6.5px;font-weight:600;display:flex;align-items:center;justify-content:center}
.agenda-item h4{font-size:7.5px;font-weight:500;margin-top:-1px}
.agenda-item p{font-size:5px;color:var(--muted);margin-top:3px}
.about-text p{font-size:5px;line-height:1.6;text-align:justify;color:var(--muted);margin-bottom:7px}
.card{position:absolute;width:136px;height:93px;background:var(--card);display:flex}
.card .photo{position:relative;width:53px;height:100%;flex:none}
.card-body{padding:10px 5px 0 8px}
.card-body h4{font-size:6.5px;font-weight:600;color:var(--blue);line-height:1.2;margin-bottom:5px}
.card-body p{font-size:4.6px;line-height:1.5;color:var(--ink)}
.step{position:absolute;width:90px;text-align:center}
.step h4{font-size:9.5px;font-weight:500;color:var(--blue);margin-bottom:5px}
.step p{font-size:5px;line-height:1.5;color:var(--muted)}
</style>
</head>
<body>

<section class="slide" style="left:49px;top:57px">
  <div class="brand" style="left:20px;top:50px"><div class="brand-mark"></div><div class="brand-name">Dr. Lena Hartmann-Vogel</div></div>
  <div class="hline" style="left:17px;top:103px;width:189px;background:var(--steel)"></div>
  <h1 class="abs" style="left:26px;top:115px;font-size:14.5px;font-weight:500;color:var(--blue);line-height:1.55">Trainings, Workshops,<br>Beratung und Coachings</h1>
  <p class="abs" style="left:26px;top:166px;width:170px;font-size:6.5px;line-height:1.6">Sed ut perspiciatis unde omnis iste natus error sit voluptatem accusantium d</p>
  <div class="hline" style="left:17px;top:201px;width:189px;background:var(--steel)"></div>
  <div class="photo" role="img" aria-label="Audience in a lecture hall with laptops" style="left:233px;top:26px;width:190px;height:188px;border:3px solid var(--navy);border-radius:8px;background:radial-gradient(circle at 50% 35%,#b4623a,#5a3626 55%,#1e1c22)"></div>
</section>

<section class="slide" style="left:518px;top:59px">
  <div class="brand" style="left:9px;top:11px"><div class="brand-mark"></div><div class="brand-name">Dr. Lena Hartmann-Vogel</div></div>
  <div class="head-rule" style="left:158px;top:11px"></div>
  <div class="slide-title" style="left:169px;top:13px;font-size:14px;color:var(--ink)">Agenda</div>
  <div class="abs" style="left:337px;top:0;width:103px;height:248px;background:var(--steel)"></div>
  <div class="agenda-item" style="left:12px;top:50px"><div class="agenda-num">01</div><div><h4>About Us</h4><p>Sed ut perspiciatis unde omnis iste natus</p></div></div>
  <div class="agenda-item" style="left:12px;top:80px"><div class="agenda-num">02</div><div><h4>Solutions</h4><p>Sed ut perspiciatis unde omnis iste natus</p></div></div>
  <div class="agenda-item" style="left:12px;top:111px"><div class="agenda-num">03</div><div><h4>Our Process</h4><p>Sed ut perspiciatis unde omnis iste natus</p></div></div>
  <div class="agenda-item" style="left:12px;top:144px"><div class="agenda-num">04</div><div><h4>Chart</h4><p>Sed ut perspiciatis unde omnis iste natus</p></div></div>
  <div class="agenda-item" style="left:12px;top:176px"><div class="agenda-num">05</div><div><h4>Benefits</h4><p>Sed ut perspiciatis unde omnis iste natus</p></div></div>
  <div class="agenda-item" style="left:12px;top:208px"><div class="agenda-num">06</div><div><h4>Lorem Ipsum</h4><p>Sed ut perspiciatis unde omnis iste natus</p></div></div>
  <div class="agenda-item" style="left:174px;top:50px"><div class="agenda-num">07</div><div><h4>How it Works</h4><p>Sed ut perspiciatis unde omnis iste natus</p></div></div>
  <div class="agenda-item" style="left:174px;top:80px"><div class="agenda-num">08</div><div><h4>Profit</h4><p>Sed ut perspiciatis unde omnis iste natus</p></div></div>
  <div class="agenda-item" style="left:174px;top:111px"><div class="agenda-num">09</div><div><h4>Services</h4><p>Sed ut perspiciatis unde omnis iste natus</p></div></div>
  <div class="agenda-item" style="left:174px;top:144px"><div class="agenda-num">10</div><div><h4>Lorem Ipsum</h4><p>Sed ut perspiciatis unde omnis iste natus</p></div></div>
  <div class="agenda-item" style="left:174px;top:176px"><div class="agenda-num">11</div><div><h4>Lorem Ipsum</h4><p>Sed ut perspiciatis unde omnis iste natus</p></div></div>
  <div class="agenda-item" style="left:174px;top:208px"><div class="agenda-num">12</div><div><h4>Thank You</h4><p>Sed ut perspiciatis unde omnis iste natus</p></div></div>
</section>

<section class="slide" style="left:47px;top:331px">
  <div class="abs" style="left:49px;top:62px;width:100px;height:100px;border:2.5px solid var(--blue);border-radius:4px"></div>
  <div class="hline" style="left:162px;top:81px;width:233px"></div>
  <h2 class="abs" style="left:180px;top:99px;font-size:22px;font-weight:500;color:var(--blue)">About us</h2>
  <p class="abs" style="left:180px;top:129px;font-size:8px;color:var(--blue)">Lorem ipsum dolor sit amet consectetur adipiscing elit</p>
  <div class="hline" style="left:162px;top:162px;width:233px"></div>
</section>

<section class="slide" style="left:518px;top:336px">
  <div class="brand" style="left:12px;top:10px"><div class="brand-mark"></div><div class="brand-name">Dr. Lena Hartmann-Vogel</div></div>
  <h2 class="abs" style="left:13px;top:43px;font-size:13.5px;font-weight:500;color:var(--blue)">About us</h2>
  <div class="abs about-text" style="left:13px;top:77px;width:215px">
    <p>Resilience describes the ability to cope with stress/crisis and the associated personal development. In this seminar, therefore, the first step is to focus on the advantages of a resilient lifestyle with the help of the 7 resilience factors. In the second step, awareness of stress and its faces is created before the focus falls on the different phases of the doctorate. Only if you recognize your own stress symptoms can you specifically search for the cause and initiate change measures.</p>
    <p>In the field of instrumental/structural stress management, models and procedures are presented that can help individuals to plan and implement their doctorate more effectively and efficiently. Aspects of prioritization and the setting of action and result goals are relevant in this context.</p>
    <p>To improve mental resilience, it is important to recognize and rethink your own thought patterns. Therefore, the examination of the inner attitude to the doctorate is an important sub-aspect. Thoughts that arise in this context are examined in more detail in order to recognize beliefs and stress-intensifying attitudes, to perceive them as such and to seize opportunities for change. There is a personal definition of the meaning of the doctorate and the awareness of one's own competences, because these are important aspects of self-esteem.</p>
  </div>
  <div class="photo" role="img" aria-label="Portrait photo of the trainer" style="left:247px;top:21px;width:173px;height:173px;border-radius:50%;background:radial-gradient(circle at 50% 40%,#d9d4cf,#9ea3a6 70%,#7d8488)"></div>
  <p class="abs" style="left:220px;top:208px;width:226px;text-align:center;font-size:8px;font-weight:500;color:var(--blue)">Dr. phil. Lena Hartmann-Vogel, MBA</p>
  <p class="abs" style="left:220px;top:220px;width:226px;text-align:center;font-size:6.5px;color:var(--blue)">Expert in Didactics and Self-Leadership</p>
</section>

<section class="slide" style="left:47px;top:603px">
  <div class="brand" style="left:12px;top:12px"><div class="brand-mark"></div><div class="brand-name">Dr. Lena Hartmann-Vogel</div></div>
  <div class="head-rule" style="left:163px;top:12px"></div>
  <div class="slide-title" style="left:177px;top:11px;line-height:1.15">Trainings, workshops,<br>consulting and coaching</div>
  <div class="card" style="left:12px;top:49px"><div class="photo" role="img" aria-label="Teacher in front of a raising-hands class" style="background:linear-gradient(160deg,#d8d3cc,#8a8682 60%,#3b3a3c)"></div><div class="card-body"><h4>For Teachers</h4><p>Design teaching that works. From didactic basics to activating methods: My trainings support you in making courses motivating, competence-oriented and stress-free, whether in person or online:</p></div></div>
  <div class="card" style="left:155px;top:49px"><div class="photo" role="img" aria-label="Hands working on a plan at a desk" style="background:linear-gradient(160deg,#6b5a4c,#3a3430 60%,#201e1f)"></div><div class="card-body"><h4>For trainers and practical instructors</h4><p>Professionally designing learning at the workplace. With these didactic basics, you will impart knowledge in practice, in a structured, motivating and competence-oriented way.</p></div></div>
  <div class="card" style="left:298px;top:49px"><div class="photo" role="img" aria-label="Doctoral candidate in a lab coat holding a folder" style="background:linear-gradient(160deg,#eef0f1,#c9ced2 60%,#4f6a70)"></div><div class="card-body"><h4>For doctoral candidates</h4><p>With clarity and balance to the doctorate. My workshops strengthen resilience, self-management and time management and teach methods of scientific project management for a focused and well-organized doctoral path.</p></div></div>
  <div class="card" style="left:12px;top:146px"><div class="photo" role="img" aria-label="Smiling student holding a notebook" style="background:linear-gradient(160deg,#cfd3d6,#8d8f90 60%,#4a4a4c)"></div><div class="card-body"><h4>For students</h4><p>Resilience and stress management will help you to master challenges in your studies with confidence and to prepare yourself optimally for starting your career:</p></div></div>
  <div class="card" style="left:155px;top:146px"><div class="photo" role="img" aria-label="Team stacking hands together" style="background:linear-gradient(160deg,#c9a98e,#7d5f52 60%,#3c3b45)"></div><div class="card-body"><h4>For Gender Equality Programs</h4><p>Staying healthy and goal-oriented in science. Stress management and resilience training support scientists in coping with stress and successfully implementing personal goals:</p></div></div>
  <div class="card" style="left:298px;top:146px"><div class="photo" role="img" aria-label="Two colleagues in a mentoring conversation" style="background:linear-gradient(160deg,#bfc8d2,#7c8696 60%,#3f4656)"></div><div class="card-body"><h4>For Mentoring Programs</h4><p>Successfully accompany and grow together. My workshops for mentors and mentees promote orientation, exchange and reflection. This is how effective mentoring that strengthens both sides can succeed:</p></div></div>
</section>

<section class="slide" style="left:514px;top:605px">
  <div class="brand" style="left:12px;top:12px"><div class="brand-mark"></div><div class="brand-name">Dr. Lena Hartmann-Vogel</div></div>
  <div class="head-rule" style="left:163px;top:12px"></div>
  <div class="slide-title" style="left:175px;top:16px">Our Process</div>
  <svg class="abs" style="left:0;top:50px" width="440" height="120" viewBox="0 0 440 120">
    <g fill="var(--sky)">
      <path d="M20 80 V45 Q20 30 35 22 L62 6 Q75 0 88 6 L115 22 Q126 28 126 40 V80 H112 V44 L75 22 L38 44 V80Z"/>
      <path d="M113 45 V80 Q113 95 128 103 L155 119 Q168 125 181 119 L208 103 Q220 95 220 80 V45 H205 V78 L168 100 L131 78 V45Z"/>
      <path d="M208 80 V45 Q208 30 223 22 L250 6 Q263 0 276 6 L303 22 Q314 28 314 40 V80 H300 V44 L263 22 L226 44 V80Z"/>
      <path d="M303 45 V80 Q303 95 318 103 L345 119 Q358 125 371 119 L398 103 Q413 95 413 80 V45 H398 V78 L361 100 L324 78 V45Z"/>
    </g>
    <g fill="#f6f7f8" stroke="#dde0e3" stroke-width="1">
      <path d="M75 14 L113 36 V80 L75 102 L37 80 V36Z"/>
      <path d="M168 26 L206 48 V92 L168 114 L130 92 V48Z"/>
      <path d="M262 14 L300 36 V80 L262 102 L224 80 V36Z"/>
      <path d="M357 26 L395 48 V92 L357 114 L319 92 V48Z"/>
    </g>
    <g fill="none" stroke="var(--sky)" stroke-width="1.4" stroke-linecap="round">
      <rect x="64" y="46" width="22" height="22" rx="1"/><path d="M68 52h12M68 57h9M68 62h6"/><circle cx="83" cy="64" r="4"/><path d="M86 67l3 3"/>
      <circle cx="168" cy="70" r="6"/><path d="M168 57v4M168 79v4M155 70h4M177 70h4M159 61l3 3M174 76l3 3M159 79l3-3M174 64l3-3"/>
      <rect x="251" y="46" width="20" height="18" rx="1"/><path d="M258 46v6h6v-6"/><circle cx="270" cy="64" r="6"/><path d="M270 61v3h2"/>
      <circle cx="357" cy="70" r="10"/><path d="M349 75l5-5 4 3 7-8M361 65h4v4"/>
    </g>
  </svg>
  <div class="step" style="left:30px;top:171px"><h4>Heading</h4><p>Sed ut perspiciatis unde omnis iste natus error sit voluptatem accusantium doloremque laudantium, totam.</p></div>
  <div class="step" style="left:123px;top:184px"><h4>Heading</h4><p>Sed ut perspiciatis unde omnis iste natus error sit voluptatem accusantium doloremque laudantium, totam.</p></div>
  <div class="step" style="left:217px;top:171px"><h4>Heading</h4><p>Sed ut perspiciatis unde omnis iste natus error sit voluptatem accusantium doloremque laudantium, totam.</p></div>
  <div class="step" style="left:312px;top:182px"><h4>Heading</h4><p>Sed ut perspiciatis unde omnis iste natus error sit voluptatem accusantium doloremque laudantium, totam.</p></div>
</section>

<section class="slide" style="left:49px;top:876px">
  <div class="brand" style="left:12px;top:12px"><div class="brand-mark"></div><div class="brand-name">Dr. Lena Hartmann-Vogel</div></div>
  <div class="head-rule" style="left:163px;top:12px"></div>
  <div class="slide-title" style="left:175px;top:15px">Chart</div>
  <svg class="abs" style="left:0;top:0" width="440" height="248" viewBox="0 0 440 248" font-family="Inter, sans-serif" font-size="3.6" fill="#333">
    <g stroke="var(--grid)" stroke-width=".6">
      <path d="M25 54H428M25 68H428M25 82H428M25 96H428M25 109H428M25 123H428M25 137H428M25 151H428M25 165H428M25 178H428M25 192H428"/>
      <path d="M57 54V192M91 54V192M125 54V192M158 54V192M192 54V192M226 54V192M259 54V192M293 54V192M327 54V192M361 54V192M394 54V192M428 54V192"/>
    </g>
    <path d="M24 54V192H428" stroke="#999" stroke-width=".6" fill="none"/>
    <g text-anchor="end"><text x="21" y="55">100</text><text x="21" y="69">90</text><text x="21" y="83">80</text><text x="21" y="97">70</text><text x="21" y="110">60</text><text x="21" y="124">50</text><text x="21" y="138">40</text><text x="21" y="152">30</text><text x="21" y="166">20</text><text x="21" y="179">10</text><text x="21" y="193">0</text></g>
    <g text-anchor="middle"><text x="40" y="201">JAN</text><text x="74" y="201">FEB</text><text x="107" y="201">MAR</text><text x="141" y="201">APR</text><text x="175" y="201">MAY</text><text x="209" y="201">JUN</text><text x="243" y="201">JUL</text><text x="276" y="201">AUG</text><text x="310" y="201">SEP</text><text x="344" y="201">OCT</text><text x="377" y="201">NOV</text><text x="411" y="201">DEC</text></g>
    <polyline fill="none" stroke="#111" stroke-width=".8" points="24,137 57,123 91,137 125,96 158,96 192,109 226,96 259,96 293,74 327,68 361,68 394,74 428,68"/>
    <g fill="#111"><circle cx="24" cy="137" r="1.6"/><circle cx="57" cy="123" r="1.6"/><circle cx="91" cy="137" r="1.6"/><circle cx="125" cy="96" r="1.6"/><circle cx="158" cy="96" r="1.6"/><circle cx="192" cy="109" r="1.6"/><circle cx="226" cy="96" r="1.6"/><circle cx="259" cy="96" r="1.6"/><circle cx="293" cy="74" r="1.6"/><circle cx="327" cy="68" r="1.6"/><circle cx="361" cy="68" r="1.6"/><circle cx="394" cy="74" r="1.6"/><circle cx="428" cy="68" r="1.6"/></g>
    <polyline fill="none" stroke="#2233dd" stroke-width=".8" points="24,178 57,151 91,165 125,123 158,109 192,137 226,123 259,137 327,82 394,109 428,82"/>
    <g fill="#2233dd"><circle cx="24" cy="178" r="1.6"/><circle cx="57" cy="151" r="1.6"/><circle cx="91" cy="165" r="1.6"/><circle cx="125" cy="123" r="1.6"/><circle cx="158" cy="109" r="1.6"/><circle cx="192" cy="137" r="1.6"/><circle cx="226" cy="123" r="1.6"/><circle cx="259" cy="137" r="1.6"/><circle cx="327" cy="82" r="1.6"/><circle cx="394" cy="109" r="1.6"/><circle cx="428" cy="82" r="1.6"/></g>
  </svg>
  <p class="abs" style="left:0;top:220px;width:440px;text-align:center;font-size:9.5px;font-weight:500">Lorem ipsum dolor sit amet consectetur adipiscing elit</p>
</section>

<section class="slide" style="left:514px;top:878px;background:var(--navy)">
  <div class="brand light" style="left:132px;top:53px"><div class="brand-mark" style="width:15px;height:15px"></div><div class="brand-name" style="font-size:12.5px">Dr. Lena Hartmann-Vogel</div></div>
  <div class="hline" style="left:134px;top:115px;width:173px;background:var(--white)"></div>
  <h2 class="abs" style="left:0;top:129px;width:440px;text-align:center;font-size:33px;font-weight:400;color:var(--white)">Thank You</h2>
  <div class="hline" style="left:134px;top:186px;width:173px;background:var(--white)"></div>
</section>

</body>
</html>
```